Tinker's Lamp sports bar beer & food menu

We need a menu design for our gastropub sports bar in L.A.'s Sawtelle Neighborhood (Little Osaka). We have a full-bar (hard liquor, craft beer, wine and cocktails) . We have a lunch and dinner menu as well as a happy hour menu. On Sundays we have a seperate menu with brunch items. The design concept is a British pub type of sports bar. We're looking for something different from our existing menu design. Ideally something cleaner and more legible. It should mesh a simple, modern sensibility with the more traditional darkened pub style of our interior design.

You can check out our Voxly page for photos of the interior/exterior:
https://www.reviewhatch.example/biz_photos/tinkers-lamp-los-angeles?tab=interior

You can view our existing menu here:
https://www.reviewhatch.example/biz_photos/tinkers-lamp-los-angeles?tab=menu

If there's an area of the design that can be a little more playful it's our highlighted event schedule so that the events will stand out.

Target Market(s)

Age of 25 and up. Sawtelle is a cultural hub that caters to a younger, moderately affluent crowd.

Industry/Entity Type

Sports Bar

Font styles to use
Sans Serif

Colors

Designer to choose colors to be used in the design.

Requirements
Must have
• Logo, highlighted event schedule (beer pong Monday, trivia Tuesday, taco Tuesday, whiskey Wednesday, karaoke Saturday). The menu should be easy to read in a darkened bar. We'll be printing on standard 8.5x11 in portrait.
Nice to have
• We're trying to have the menu take up as few pages as possible.
Should not have
• We're trying to have the menu take up as few pages as possible. Food photography isn't necessary. A cover isn't necessary. Please avoid clip art of food.

```html
<!DOCTYPE html>
<html lang="en">
<head>
<meta charset="utf-8">
<title>Tinker's Lamp — Pub &amp; Restaurant Menu</title>
<link rel="stylesheet" href="https://fonts.googleapis.com/css2?family=Playfair+Display:wght@900&family=Montserrat:wght@600;700&family=Open+Sans:wght@400&family=Cinzel:wght@400&family=Courier+Prime&display=swap">
<style>
  :root {
    --ink-navy: #0c2431;
    --ornament-copper: #b87a4b;
    --heading-orange: #f39349;
    --item-yellow: #f7dc72;
    --text-white: #ffffff;
    --band-grey: #d6d6d6;
    --band-edge: #b0b0b0;
    --band-text: #1a1a1a;
  }
  html, body {
    margin: 0;
    padding: 0;
    overflow: hidden;
    background: var(--ink-navy);
  }
  .menu {
    position: relative;
    width: 848px;
    height: 1200px;
    overflow: hidden;
    background: var(--ink-navy);
    color: var(--text-white);
    font-family: "Open Sans", Arial, sans-serif;
  }
  .ornament {
    position: absolute;
    left: 0;
    top: 0;
    width: 848px;
    height: 150px;
    background: radial-gradient(ellipse at 50% 0%, rgba(184,122,75,0.30), rgba(184,122,75,0.10) 60%, rgba(12,36,49,0) 100%);
  }
  .brand-mark {
    position: absolute;
    left: 190px;
    top: 36px;
    width: 58px;
    height: 58px;
    border: 4px solid var(--text-white);
    box-sizing: border-box;
  }
  .brand-name {
    position: absolute;
    left: 264px;
    top: 34px;
    margin: 0;
    font-family: "Montserrat", Arial, sans-serif;
    font-weight: 600;
    font-size: 56px;
    line-height: 66px;
    color: var(--text-white);
    white-space: nowrap;
  }
  .brand-tagline {
    position: absolute;
    left: 300px;
    top: 104px;
    width: 334px;
    text-align: center;
    font-family: "Cinzel", Georgia, serif;
    font-size: 15px;
    line-height: 20px;
    letter-spacing: 7px;
    color: var(--text-white);
  }
  .section {
    position: absolute;
    text-align: center;
  }
  .col-left { left: 22px; width: 372px; }
  .col-right { left: 462px; width: 364px; }
  .section-title {
    position: absolute;
    margin: 0;
    font-family: "Playfair Display", Georgia, serif;
    font-weight: 900;
    font-size: 37px;
    line-height: 34px;
    text-transform: uppercase;
    color: var(--heading-orange);
    text-align: center;
    white-space: nowrap;
  }
  .section-list {
    position: absolute;
    margin: 0;
    padding: 0;
    list-style: none;
    text-align: center;
  }
  .dish-name {
    display: block;
    font-family: "Montserrat", Arial, sans-serif;
    font-weight: 700;
    font-size: 16px;
    color: var(--item-yellow);
    white-space: nowrap;
  }
  .dish-desc {
    display: block;
    font-size: 17.4px;
    white-space: nowrap;
  }
  .title-burgers { left: 22px; width: 372px; top: 153px; }
  .list-burgers { left: 22px; width: 372px; top: 223px; line-height: 29.2px; }
  .title-bites { left: 462px; width: 364px; top: 151px; }
  .list-bites { left: 462px; width: 364px; top: 195px; line-height: 26.1px; }
  .title-flatbreads { left: 462px; width: 364px; top: 624px; }
  .list-flatbreads { left: 462px; width: 364px; top: 665px; line-height: 26.1px; }
  .divider {
    position: absolute;
    left: 422px;
    top: 187px;
    width: 4px;
    height: 926px;
    background: var(--text-white);
  }
  .events-band {
    position: absolute;
    left: 19px;
    top: 1139px;
    width: 798px;
    height: 50px;
    background: var(--band-grey);
    border: 1px solid var(--band-edge);
    box-sizing: border-box;
    display: flex;
    align-items: center;
    justify-content: center;
    font-family: "Courier Prime", "Courier New", monospace;
    font-size: 16.5px;
    color: var(--band-text);
    white-space: nowrap;
  }
</style>
</head>
<body>
<main class="menu">
  <div class="ornament" role="img" aria-label="Copper filigree swirl ornament across the top of the menu"></div>

  <header>
    <div class="brand-mark" aria-hidden="true"></div>
    <h1 class="brand-name">Tinker's Lamp</h1>
    <div class="brand-tagline">PUB &amp; RESTAURANT</div>
  </header>

  <section>
    <h2 class="section-title title-burgers">Burgers and<br>Sandwiches</h2>
    <ul class="section-list list-burgers">
      <li><span class="dish-name">Chicken Sandwich...$12</span>
        <span class="dish-desc">Chicken Breast, Applewood Bacon, Butter<br>Lettuce, White Cheddar, Avocado and<br>Tomato Served on Sourdough Bread</span></li>
      <li><span class="dish-name">Buttermilk Fried Chicken...$13</span>
        <span class="dish-desc">Coleslaw, Provolone, Tomato, and a Spiced<br>Mayonnaise on a Pretzel Roll</span></li>
      <li><span class="dish-name">Short Rib Sandwich...$13</span>
        <span class="dish-desc">Beef Shorts, Mayo, Tomato, Caramelized<br>Onions, Arugula, Pepper Jack Cheese<br>Served on Sourdough Bread</span></li>
      <li><span class="dish-name">Grilled Cheese Sandwich...$10</span>
        <span class="dish-desc">Cheese, Provolone and Cheddar Cheese</span></li>
      <li><span class="dish-name">Tinker's Lamp Burger...$14</span>
        <span class="dish-desc">Sharp Cheddar, Arugula, Roasted Shallots,<br>Bacon Jam with Malt Aioli</span></li>
      <li><span class="dish-name">The Truffle Burger...$15</span>
        <span class="dish-desc">Caramelized Onions, Arugula, Truffle<br>Pecorino, Truffle Mayo and Truffle Fries</span></li>
      <li><span class="dish-name">The Sloppy Joe..$10</span>
        <span class="dish-desc">Shredded Lettuce and Sharp Cheddar</span></li>
      <li><span class="dish-name">Veggie Burger...$12</span>
        <span class="dish-desc">Concoction of kale, Tomato, Avocado,<br>Sharp Cheddar with a Balsamic Reduction</span></li>
      <li><span class="dish-name">Flat Iron Steak Sandwich...$16</span>
        <span class="dish-desc">Arugula, Peppers, Fontina, Onion and Mayo</span></li>
      <li><span class="dish-name">Chicken Spinach Wrap...$10</span>
        <span class="dish-desc">Chicken, Bacon, Lettuce, Tomato, Avocado,<br>Ranch and Mayo</span></li>
      <li><span class="dish-name">Fried Chicken Sliders (4)...$12</span>
        <span class="dish-desc">Coleslaw, Lime Sriracha Sauce</span></li>
    </ul>
  </section>

  <div class="divider" aria-hidden="true"></div>

  <section>
    <h2 class="section-title title-bites">Big Dog Bites</h2>
    <ul class="section-list list-bites">
      <li><span class="dish-name">Atlantic Cod Fish N' Chips...$15</span>
        <span class="dish-desc">House Tartar Sauce, Vinegar and Lemon<br>Wedge</span></li>
      <li><span class="dish-name">Oven Roasted ½ Roasted Chicken...$16</span>
        <span class="dish-desc">Boneless Chicken, Broccolini, Fingerling<br>Potatoes, Topped with Chimichurri Sauce</span></li>
      <li><span class="dish-name">Black Mussels...$17</span>
        <span class="dish-desc">Tequila Chipotle Sauce, Cilantro and<br>Cherry Tomatoes</span></li>
      <li><span class="dish-name">Pan Seared Salmon...$19</span>
        <span class="dish-desc">Sushi Grade Salmon, Spaghetti Squash,<br>Zucchini, Cherry Tomatoes<br>In a Lemon Caper Beurre Blanc</span></li>
      <li><span class="dish-name">Flat Iron Steak...$22</span>
        <span class="dish-desc">French Fries, Baby Arugula in a Light<br>peppercorn Sauce</span></li>
    </ul>
  </section>

  <section>
    <h2 class="section-title title-flatbreads">Flatbreads</h2>
    <ul class="section-list list-flatbreads">
      <li><span class="dish-name">Margherita...$12</span>
        <span class="dish-desc">Fresh Mozzarella, Roma Tomatoes and<br>Fresh Italian Basil</span></li>
      <li><span class="dish-name">Vegetarian...$13</span>
        <span class="dish-desc">Brussel Sprouts, Peppers, Onions,<br>Zucchini, Goat Cheese, Smoked<br>Mozzarella</span>
        <span class="dish-desc">Topped with a Balsamic Reduction</span></li>
      <li><span class="dish-name">Prosciutto &amp;Arugula..$14</span>
        <span class="dish-desc">Red Onion, Parmesan, Mozzarella</span></li>
      <li><span class="dish-name">Portobello &amp; Truffle...$14</span>
        <span class="dish-desc">Portobello White Mushroom, Fontina,<br>Drizzled with Truffle Oil</span></li>
      <li><span class="dish-name">Chicken Tikka Masala...$14</span>
        <span class="dish-desc">Tandoori Chicken, Fontini and Raita</span></li>
      <li><span class="dish-name">The Tinker's Lamp...$15</span>
        <span class="dish-desc">Meatballs, Sausage, Chorizo, Mozzarella<br>and Fresen</span></li>
    </ul>
  </section>

  <footer class="events-band">Beer Pong Monday, Trivia &amp; Taco Tuesday, Whiskey Wednesday, Karaoke Saturday</footer>
</main>
</body>
</html>
```